Orvane Group Business Card

Building Management company based in Sydney, Australia. We provide onsite management for commercial and residential buildings.
I would like a sophisticated minimalist design that indicates that we provide a high-end service. I would like a silver or metal look background or something similar.
The business card should have:
Name
Title
email
Office Phone
Mobile
Address
Website
The services that we provide should be prominent:
Building Management - Concierge - Caretaking - Cleaning

```html
<!DOCTYPE html>
<html lang="en">
<head>
<meta charset="utf-8">
<title>Orvane Group Business Card</title>
<link href="https://fonts.googleapis.com/css2?family=Quicksand:wght@500;600;700&display=swap" rel="stylesheet">
<style>
  :root {
    --stage: #d9d9d9;
    --metal-light: #f2f3f4;
    --metal-mid: #c9cccf;
    --metal-dark: #a7abaf;
    --accent-blue: #1f66b3;
    --text-dark: #1b1c1e;
    --text-soft: #3d4044;
    --rule: #8d9195;
  }
  * { margin: 0; padding: 0; box-sizing: border-box; }
  html, body {
    width: 1200px; height: 900px; overflow: hidden;
    background: var(--stage);
    font-family: "Quicksand", sans-serif;
  }
  .stage {
    width: 1200px; height: 900px;
    display: flex; flex-direction: column;
    align-items: center; justify-content: center; gap: 48px;
  }
  .card {
    position: relative;
    width: 660px; height: 377px;
    background:
      repeating-linear-gradient(90deg, rgba(255,255,255,0.08) 0 1px, rgba(0,0,0,0.03) 1px 3px),
      linear-gradient(135deg, var(--metal-light) 0%, var(--metal-mid) 38%, var(--metal-light) 58%, var(--metal-dark) 100%);
    color: var(--text-dark);
    box-shadow: 0 6px 16px rgba(0,0,0,0.18);
  }
  .brand {
    display: flex; align-items: center; gap: 12px;
    font-weight: 700; letter-spacing: 1px; color: var(--text-dark);
  }
  .brand-mark { width: 14px; height: 14px; background: var(--accent-blue); }
  .card-front {
    display: flex; flex-direction: column;
    align-items: center; justify-content: center; gap: 22px;
  }
  .card-front .brand { font-size: 40px; }
  .services {
    display: flex; align-items: center; gap: 12px;
    font-size: 15px; font-weight: 700; letter-spacing: 1.5px;
    text-transform: uppercase; color: var(--text-soft);
  }
  .services .sep { width: 5px; height: 5px; background: var(--accent-blue); }
  .card-back .brand {
    position: absolute; right: 60px; top: 92px; font-size: 30px;
  }
  .holder { position: absolute; left: 60px; top: 86px; }
  .holder-name { font-size: 27px; font-weight: 700; line-height: 1.1; }
  .holder-title { font-size: 15px; font-weight: 600; color: var(--accent-blue); margin-top: 2px; }
  .divider {
    position: absolute; left: 60px; right: 60px; top: 160px;
    height: 1px; background: var(--rule);
  }
  .contact {
    position: absolute; right: 60px; bottom: 34px;
    list-style: none; text-align: right;
    font-size: 16px; font-weight: 600; line-height: 27px;
  }
  .contact li { display: flex; justify-content: flex-end; align-items: center; gap: 10px; }
  .contact svg { width: 12px; height: 12px; fill: none; stroke: var(--accent-blue); stroke-width: 1.6; }
</style>
</head>
<body>
<main class="stage">
  <section class="card card-front">
    <div class="brand"><span class="brand-mark"></span><span>ORVANE GROUP</span></div>
    <p class="services">
      <span>Building Management</span><span class="sep"></span>
      <span>Concierge</span><span class="sep"></span>
      <span>Caretaking</span><span class="sep"></span>
      <span>Cleaning</span>
    </p>
  </section>

  <section class="card card-back">
    <div class="holder">
      <p class="holder-name">Callum Reyes</p>
      <p class="holder-title">Managing Director</p>
    </div>
    <div class="brand"><span class="brand-mark"></span><span>ORVANE GROUP</span></div>
    <div class="divider"></div>
    <ul class="contact">
      <li>123.456.7890
        <svg viewBox="0 0 12 12"><rect x="3" y="1" width="6" height="10" rx="1"/></svg></li>
      <li>123.456.7890
        <svg viewBox="0 0 12 12"><path d="M2 4 Q6 1 10 4 L9 6 L7 5 L5 5 L3 6 Z M3 7 H9 V10 H3 Z"/></svg></li>
      <li>info@youremail.com
        <svg viewBox="0 0 12 12"><rect x="1" y="3" width="10" height="7"/><path d="M1 3 L6 7 L11 3"/></svg></li>
      <li>www.website.com
        <svg viewBox="0 0 12 12"><path d="M5 7 L7 5 M4 6 L2 8 A1.4 1.4 0 0 0 4 10 L6 8 M8 6 L10 4 A1.4 1.4 0 0 0 8 2 L6 4"/></svg></li>
      <li>Level 4, 28 Harbour Lane, Sydney NSW 2000
        <svg viewBox="0 0 12 12"><path d="M6 11 C3 7.5 2.5 6 2.5 4.5 A3.5 3.5 0 0 1 9.5 4.5 C9.5 6 9 7.5 6 11 Z"/><circle cx="6" cy="4.5" r="1.2"/></svg></li>
    </ul>
  </section>
</main>
</body>
</html>
```